@CLLovedale Meaddow Company

Honey Jar label. Would like it to be square (diamond shape). Will need a space for my city and state. will need a space for my phone number. Will need to have "Grade A" on the label and "product of USA" "Honey" must be larger then any other word. Black background. Label needs to look old fashion (cir 1880s) Sketch of Mt #2Raainier attached that I have the rights to use.

Like the look of this https://shop.pellowbrint.com/pbshop/item.php?nodeid=16

Same label will also be used for a run of a limited supply of honey. So I will need one that also has "Pipkin's private batch". Pipkin is my daughter"s rabbit

```html
<!DOCTYPE html>
<html lang="en">
<head>
<meta charset="utf-8">
<title>CLLovedale Meaddow Company – Honey Labels</title>
<link rel="stylesheet" href="https://fonts.googleapis.com/css2?family=Oranienbaum&family=Pinyon+Script&family=Cinzel:wght@600&display=swap">
<style>
  :root {
    --bg-top: #efdba2;
    --bg-mid: #e0a83a;
    --bg-bottom: #d04a00;
    --label-black: #000000;
    --gold: #deaa3c;
    --company-orange: #e2632a;
    --ornament-brown: #8b4b12;
    --rule-brown: #7a4a16;
    --cream: #f3ead6;
  }
  html, body {
    margin: 0;
    padding: 0;
    width: 1200px;
    height: 900px;
    overflow: hidden;
  }
  .canvas {
    display: block;
    width: 1200px;
    height: 900px;
  }
  .company-name {
    font-family: "Oranienbaum", serif;
    font-size: 29px;
    fill: var(--company-orange);
  }
  .script-caption {
    font-family: "Pinyon Script", cursive;
    font-size: 23px;
    fill: var(--gold);
  }
  .origin-mark, .grade-mark {
    font-family: "Oranienbaum", serif;
    font-size: 42px;
    fill: var(--gold);
  }
  .product-word {
    font-family: "Oranienbaum", serif;
    font-size: 118px;
    fill: var(--gold);
  }
  .edge-detail {
    font-family: "Cinzel", serif;
    font-weight: 600;
    font-size: 12.5px;
    fill: var(--cream);
  }
  .banner-text {
    font-family: "Cinzel", serif;
    font-weight: 600;
    font-size: 16px;
    fill: var(--cream);
  }
  .rule { stroke: var(--rule-brown); stroke-width: 1.2; fill: none; }
</style>
</head>
<body>
<svg class="canvas" viewBox="0 0 1200 900" xmlns="http://www.w3.org/2000/svg">
  <defs>
    <linearGradient id="backdrop" x1="0" y1="0" x2="0" y2="1">
      <stop offset="0" stop-color="var(--bg-top)"/>
      <stop offset="0.3" stop-color="var(--bg-mid)"/>
      <stop offset="1" stop-color="var(--bg-bottom)"/>
    </linearGradient>
    <linearGradient id="sceneTones" x1="0" y1="0" x2="0" y2="1">
      <stop offset="0" stop-color="#d9dcc0"/>
      <stop offset="0.35" stop-color="#f0c8a0"/>
      <stop offset="0.6" stop-color="#8a4448"/>
      <stop offset="1" stop-color="#6f8a2e"/>
    </linearGradient>
    <radialGradient id="ornamentTones" cx="0.5" cy="0.5" r="0.6">
      <stop offset="0" stop-color="#a35a18"/>
      <stop offset="1" stop-color="#6e3a0e"/>
    </radialGradient>

    <g id="honey-label">
      <polygon class="label-field" points="306,157 598,450 306,742 14,450" fill="var(--label-black)"/>

      <path class="ornament-top" d="M306 190 Q330 215 388 258 L224 258 Q282 215 306 190 Z" fill="url(#ornamentTones)" role="img" aria-label="Victorian scrollwork ornament"/>
      <line class="rule" x1="218" y1="268" x2="394" y2="268"/>
      <line class="rule" x1="222" y1="274" x2="390" y2="274"/>
      <line class="rule" x1="78" y1="400" x2="210" y2="268"/>
      <line class="rule" x1="402" y1="268" x2="534" y2="400"/>

      <text class="company-name" x="306" y="322" text-anchor="middle" textLength="252" lengthAdjust="spacingAndGlyphs">CLLOVEDALE MEADDOW CO.</text>

      <ellipse class="vignette-frame" cx="306" cy="418" rx="131" ry="89" fill="none" stroke="var(--gold)" stroke-width="1.5"/>
      <ellipse class="mountain-vignette" cx="306" cy="418" rx="126" ry="84" fill="url(#sceneTones)" role="img" aria-label="Sketch of a snow-capped mountain above green foothills under a cloudy sky"/>

      <text class="script-caption" x="110" y="434" text-anchor="middle">Product of</text>
      <text class="origin-mark" x="108" y="476" text-anchor="middle">USA</text>
      <text class="script-caption" x="500" y="440" text-anchor="middle">Grade</text>
      <text class="grade-mark" x="498" y="482" text-anchor="middle">A</text>

      <text class="edge-detail" transform="translate(136 551) rotate(45)" text-anchor="middle" textLength="150" lengthAdjust="spacingAndGlyphs">TEL. 1-800-MEADOWS</text>
      <text class="edge-detail" transform="translate(484 547) rotate(-45)" text-anchor="middle" textLength="150" lengthAdjust="spacingAndGlyphs">FERNWICK, OREGON</text>

      <text class="product-word" x="306" y="606" text-anchor="middle" textLength="206" lengthAdjust="spacingAndGlyphs">HONEY</text>

      <line class="rule" x1="222" y1="622" x2="390" y2="622"/>
      <line class="rule" x1="226" y1="628" x2="386" y2="628"/>
      <path class="ornament-bottom" d="M222 638 L390 638 Q332 680 306 710 Q280 680 222 638 Z" fill="url(#ornamentTones)" role="img" aria-label="Victorian scrollwork ornament"/>
    </g>
  </defs>

  <rect class="backdrop" width="1200" height="900" fill="url(#backdrop)"/>

  <use class="label-standard" href="#honey-label"/>

  <g class="label-private-batch">
    <use href="#honey-label" x="587"/>
    <path class="batch-banner" d="M765 488 Q892 470 1018 488 L1018 516 Q892 500 765 516 Z"
          fill="var(--ornament-brown)" stroke="var(--gold)" stroke-width="1.5"/>
    <text class="banner-text" x="892" y="503" text-anchor="middle" textLength="232" lengthAdjust="spacingAndGlyphs">PIPKIN'S PRIVATE BATCH</text>
  </g>
</svg>
</body>
</html>
```